Brightwave Reach - Business Card

We need a business card for a Social Media Marketing company that specializes in online marketing for small businesses in Canada using common Social Media platforms such as Pixlora, Chatterly, Blinkpost & Quibber.

I have uploaded a copy of our logo which I would like utilized in the business card. We would like the business card to be modern yet classy design.

Our website is www.brightwavereach.ca

Industry/Entity Type

Marketing

Contact Information for Business Card

Email: info@brightwavereach.ca
Website: www.brightwavereach.ca
Telephone: 604-555-0193

Colors

Designer to choose colors to be used in the design.

Requirements
Must have
• Social Media icons on reverse
• Please add some designs with color.

```html
<!DOCTYPE html>
<html lang="en">
<head>
<meta charset="utf-8">
<title>Brightwave Reach – Business Card</title>
<link rel="stylesheet" href="https://fonts.googleapis.com/css2?family=Roboto:wght@400;500;700;900&display=swap">
<style>
  :root {
    --backdrop: #dcdcdc;
    --card-dark: #3a3d40;
    --card-light: #efefef;
    --ink-light: #ffffff;
    --ink-dark: #3b3d40;
    --emblem-core: rgba(244, 244, 244, 0.55);
    --emblem-edge: rgba(244, 244, 244, 0);
  }
  * { margin: 0; padding: 0; box-sizing: border-box; }
  html, body {
    width: 1200px; height: 960px; overflow: hidden;
    background: var(--backdrop);
    font-family: "Roboto", Arial, sans-serif;
  }
  .canvas { position: relative; width: 1200px; height: 960px; }

  .card { position: absolute; width: 600px; height: 343px; overflow: hidden; }
  .card--front { left: 314px; top: 113px; background: var(--card-dark); color: var(--ink-light); }
  .card--back { left: 311px; top: 472px; background: var(--card-light); color: var(--ink-dark); }

  .brand-name {
    position: absolute; left: 47px; top: 168px; top: 56px;
    font-weight: 900; font-size: 29px; line-height: 31px;
    letter-spacing: 1px; text-transform: uppercase;
  }
  .accent-bar { position: absolute; left: 0; top: 184px; width: 12px; height: 37px; background: var(--ink-light); }
  .person-name { position: absolute; left: 47px; top: 181px; font-weight: 500; font-size: 19px; letter-spacing: .3px; }
  .person-title { position: absolute; left: 47px; top: 207px; font-size: 14px; letter-spacing: .3px; }

  .contact-list { position: absolute; left: 48px; top: 243px; list-style: none; }
  .contact-list li { display: flex; align-items: center; height: 19px; font-size: 14px; }
  .contact-list svg { width: 13px; height: 13px; margin-right: 9px; fill: var(--ink-light); }

  .emblem {
    position: absolute; left: 296px; top: 14px; width: 272px; height: 329px;
    background: radial-gradient(ellipse 50% 46% at 50% 48%, var(--emblem-core) 0%, rgba(244,244,244,.3) 55%, var(--emblem-edge) 100%);
  }

  .back-brand {
    position: absolute; left: 0; right: 0; top: 128px; text-align: center;
    font-weight: 900; font-size: 31px; line-height: 34px; letter-spacing: .5px;
    text-transform: uppercase;
  }
  .social-row {
    position: absolute; left: 0; right: 0; top: 282px;
    display: flex; justify-content: center; gap: 16px; list-style: none;
    font-size: 13px; font-weight: 500;
  }
  .social-row li { display: flex; align-items: center; gap: 6px; }
  .social-dot {
    width: 26px; height: 26px; border: 2px solid var(--ink-dark);
    border-radius: 50%; background: var(--ink-dark);
  }
</style>
</head>
<body>
<main class="canvas">
  <section class="card card--front">
    <div class="brand-name">Brightwave<br>Reach</div>
    <div class="accent-bar"></div>
    <div class="person-name">OWEN TREMBLAY</div>
    <div class="person-title">CEO/FOUNDER</div>
    <ul class="contact-list">
      <li><svg viewBox="0 0 24 24"><path d="M6.6 10.8a15.1 15.1 0 0 0 6.6 6.6l2.2-2.2c.3-.3.7-.4 1-.2 1.1.4 2.3.6 3.6.6.6 0 1 .4 1 1V20c0 .6-.4 1-1 1C10.6 21 3 13.4 3 4c0-.6.4-1 1-1h3.5c.6 0 1 .4 1 1 0 1.3.2 2.5.6 3.6.1.3 0 .7-.2 1z"/></svg>604-555-0193</li>
      <li><svg viewBox="0 0 24 24"><path d="M2 5h20v14H2zm2 2v.5l8 5 8-5V7l-8 5z"/></svg>info@brightwavereach.ca</li>
      <li><svg viewBox="0 0 24 24"><circle cx="12" cy="12" r="10"/><path d="M2 12h20M12 2c3 3 3 17 0 20M12 2c-3 3-3 17 0 20" stroke="#3a3d40" stroke-width="1.6" fill="none"/></svg>www.brightwavereach.ca</li>
    </ul>
    <div class="emblem" role="img" aria-label="Large distressed white emblem decoration"></div>
  </section>

  <section class="card card--back">
    <div class="back-brand">Brightwave<br>Reach</div>
    <ul class="social-row">
      <li><span class="social-dot"></span>Chatterly</li>
      <li><span class="social-dot"></span>Pixlora</li>
      <li><span class="social-dot"></span>Quibber</li>
    </ul>
  </section>
</main>
</body>
</html>
```